Weightloss company needs Business Card

We want a business card that is clean and professional, yet portrays that we are a friendly, innovative, and versatile program designed to fit the needs of our clients.
I would like there to be 2 sides, one side having an appointment card, and the other side containing the logo and business information. There can be decorations on both sides. The logo is attached.

Target Market(s)

Men and women 40-60

Industry/Entity Type

Business

Contact Information for Business Card

Font styles to use
Sans Serif

Requirements
Must have
• The logo, space for business information
Nice to have
• The colors in the logo
Should not have
• No pictures of people or food

```html
<!DOCTYPE html>
<html lang="en">
<head>
<meta charset="utf-8">
<title>Turnwell Weightloss – Business Card</title>
<link href="https://fonts.googleapis.com/css2?family=Montserrat:wght@700;800&family=Questrial&display=swap" rel="stylesheet">
<style>
  :root {
    --backdrop: #e6e7ea;
    --card: #ffffff;
    --sky: #4fc6ef;
    --red: #e8243b;
    --ink: #111111;
    --line: #222222;
    --white: #ffffff;
  }
  * { box-sizing: border-box; margin: 0; padding: 0; }
  html, body {
    width: 1200px; height: 900px; overflow: hidden;
    background: var(--backdrop);
    font-family: "Questrial", "Century Gothic", sans-serif;
  }
  .canvas { position: relative; width: 1200px; height: 900px; }

  .card {
    position: absolute; left: 250px; width: 700px; height: 400px;
    background: var(--card); border-radius: 26px; overflow: hidden;
    box-shadow: 0 14px 30px rgba(0,0,0,.18);
  }
  .card--appointment { top: 34px; }
  .card--contact { top: 466px; }

  .brand {
    position: absolute; z-index: 2; display: flex; align-items: center; gap: 10px;
    font-family: "Montserrat", sans-serif; font-weight: 800; white-space: nowrap;
    color: var(--red); font-size: 26px; letter-spacing: .3px; line-height: 1;
  }
  .brand__dot { width: 13px; height: 13px; border-radius: 50%; background: var(--red); }
  .card--appointment .brand { top: 50px; right: 40px; }
  .card--contact .brand { top: 112px; right: 32px; }

  .appointment { position: absolute; left: 60px; top: 196px; width: 580px; }
  .appointment__title { color: var(--red); font-size: 17px; letter-spacing: .5px; margin-bottom: 16px; }
  .field { display: flex; align-items: flex-end; gap: 12px; margin-bottom: 26px; font-size: 18px; color: var(--ink); }
  .field__label { width: 60px; }
  .field__line { flex: 1; border-bottom: 1.5px solid var(--line); height: 1px; margin-bottom: 5px; }

  .card__art { position: absolute; inset: 0; z-index: 1; }

  .contact { position: absolute; z-index: 2; left: 60px; top: 196px; color: var(--white); }
  .contact__name {
    font-family: "Montserrat", sans-serif; font-weight: 700;
    color: var(--ink); font-size: 26px; letter-spacing: .5px;
  }
  .contact__role { font-size: 17px; margin: 2px 0 10px; letter-spacing: .5px; }
  .contact__address { font-size: 17px; line-height: 1.3; margin-bottom: 10px; }
  .contact__row { display: flex; align-items: center; gap: 10px; font-size: 17px; line-height: 1.5; }
  .contact__icon { width: 16px; height: 16px; flex: none; }
</style>
</head>
<body>
<main class="canvas">

  <section class="card card--appointment" aria-label="Appointment side">
    <div class="brand"><span class="brand__dot"></span>Turnwell Weightloss</div>
    <div class="appointment">
      <p class="appointment__title">APPOINTMENT</p>
      <div class="field"><span class="field__label">Name:</span><span class="field__line"></span></div>
      <div class="field"><span class="field__label">Date:</span><span class="field__line"></span></div>
      <div class="field"><span class="field__label">Time:</span><span class="field__line"></span></div>
    </div>
  </section>

  <section class="card card--contact" aria-label="Contact side">
    <svg class="card__art" width="700" height="400" viewBox="0 0 700 400" aria-hidden="true">
      <circle cx="195" cy="335" r="252" fill="var(--red)" stroke="#000" stroke-width="1.5"/>
      <circle cx="180" cy="340" r="240" fill="var(--sky)" stroke="#000" stroke-width="1.5"/>
    </svg>

    <div class="brand"><span class="brand__dot"></span>Turnwell Weightloss</div>

    <div class="contact">
      <h1 class="contact__name">MARCO ELLISON</h1>
      <p class="contact__role">DIRECTOR</p>
      <p class="contact__address">Harbor Lane, 21500<br>Seaview, Coastland</p>
      <p class="contact__row">
        <svg class="contact__icon" viewBox="0 0 24 24"><path fill="#000" d="M6.6 10.8a15 15 0 0 0 6.6 6.6l2.2-2.2a1 1 0 0 1 1-.25 11.4 11.4 0 0 0 3.6.57 1 1 0 0 1 1 1V20a1 1 0 0 1-1 1A17 17 0 0 1 3 4a1 1 0 0 1 1-1h3.5a1 1 0 0 1 1 1c0 1.25.2 2.45.57 3.570a1 1 0 0 1-.25 1z"/></svg>
        +330 2100-4875
      </p>
      <p class="contact__row">
        <svg class="contact__icon" viewBox="0 0 24 24"><rect x="2" y="5" width="20" height="14" fill="none" stroke="#000" stroke-width="2"/><path d="M2 5l10 8 10-8" fill="none" stroke="#000" stroke-width="2"/></svg>
        info@turnwellweightloss.com
      </p>
      <p class="contact__row">
        <svg class="contact__icon" viewBox="0 0 24 24"><circle cx="12" cy="12" r="10" fill="none" stroke="#000" stroke-width="2"/><ellipse cx="12" cy="12" rx="4" ry="10" fill="none" stroke="#000" stroke-width="1.6"/><path d="M2 12h20" stroke="#000" stroke-width="1.6"/></svg>
        www.turnwellweightloss.com
      </p>
    </div>
  </section>

</main>
</body>
</html>
```